Web page design for a startup, no coding

Quorvix is a Data mining startup helping companies get data from websites. We’re looking to revamp our website to make it more professional and conversation friendly.
I need a designer to design the website in PSD and Once the PSD is done, the HTML design will be awarded as a separate job. We’ll need continues improvements to the design based on the user behaviour in the site and this can be a long term work for the right designer.
Read the details on the attached document
Target Market(s)
Big data, Data Mining
Industry/Entity Type
Business Software
Number of Pages Required
5+ page
Requirements
Must have
- Refer to the doc
Nice to have
- Refer to the doc
Should not have
- Refer to the doc

```html
<!DOCTYPE html>
<html lang="en">
<head>
<meta charset="utf-8">
<title>Quorvix – Turn Websites Into Structured Data Feeds</title>
<link rel="stylesheet" href="https://fonts.googleapis.com/css2?family=Open+Sans:wght@300;400;600;700&display=swap">
<style>
:root{
  --orange:#f6a01a;
  --orange-dark:#e48f0c;
  --ink:#3b3b3b;
  --text:#6d6d6d;
  --muted:#9a9a9a;
  --line:#dcdcdc;
  --soft:#f1f1f1;
  --grey-hex:#7a7a7a;
  --white:#ffffff;
}
*{box-sizing:border-box;margin:0;padding:0}
html,body{width:1200px;height:2580px;overflow:hidden}
body{font-family:"Open Sans",Arial,sans-serif;color:var(--ink);background:var(--white);position:relative}
.container{position:absolute;left:160px;width:880px}

/* Hero */
.hero{position:absolute;top:0;left:0;width:1200px;height:556px;overflow:hidden}
.hero-photo{position:absolute;inset:0;background:linear-gradient(120deg,#8d8f90 0%,#b4b5b3 35%,#9a9b97 60%,#6f7370 100%)}
.hero-shade{position:absolute;inset:0;background:rgba(40,40,40,.25)}
.nav{position:absolute;top:26px;left:160px;width:880px;height:44px;display:flex;align-items:center;justify-content:space-between}
.brand{display:flex;align-items:center;gap:10px;color:var(--white);font-size:30px;font-weight:600;letter-spacing:.5px}
.brand-mark{width:14px;height:14px;background:var(--white)}
.nav-links{display:flex;align-items:center;gap:30px;font-size:15px;color:var(--white);font-weight:600}
.nav-cta{background:var(--orange);padding:8px 16px}
.hero-title{position:absolute;top:236px;left:0;width:1200px;text-align:center;color:var(--white);font-size:42px;font-weight:600;line-height:56px}
.hero-sub{position:absolute;top:302px;left:270px;width:660px;text-align:center;color:var(--white);font-size:16px;line-height:24px}
.btn{display:inline-block;background:var(--orange);color:var(--white);font-weight:600;font-size:14px;text-align:center}
.hero-btn{position:absolute;top:370px;left:528px;width:144px;height:40px;line-height:40px}
.dots{position:absolute;top:558px;left:0;width:1200px;display:flex;justify-content:center;gap:10px}
.dot{width:12px;height:12px;border-radius:50%;background:#5a5a5a}
.dot.active{background:#c4c4c4}

/* Clients */
.clients-title{position:absolute;top:614px;left:0;width:1200px;text-align:center;color:var(--orange);font-size:28px;font-weight:400}
.clients{top:686px;height:80px;display:flex;gap:10px}
.client{flex:1;border:2px solid var(--line);display:flex;align-items:center;justify-content:center;font-size:19px;font-weight:600;color:var(--ink)}

/* Use cases */
.uses{position:absolute;top:800px;left:0;width:1200px;height:540px;background:var(--soft)}
.uses-title{position:absolute;top:58px;left:0;width:1200px;text-align:center;font-size:28px;font-weight:600;line-height:40px;color:var(--ink)}
.use{position:absolute;width:220px}
.use h3{font-size:17px;font-weight:600;color:var(--ink);margin-bottom:6px}
.use p{font-size:12px;line-height:17px;color:var(--muted)}
.use.left{left:310px}
.use.right{left:700px}
.use-icon{position:absolute;width:40px;height:40px;border:2px solid var(--orange);border-radius:6px;background:var(--white)}
.use-icon.left{left:548px}
.use-icon.right{left:624px}

/* Why us */
.why-title{position:absolute;top:1392px;left:0;width:1200px;text-align:center;font-size:32px;font-weight:600;color:var(--ink)}
.hex{position:absolute;top:1474px;width:216px;height:280px}
.hex svg{position:absolute;inset:0}
.hex-body{position:absolute;top:82px;left:18px;width:180px;text-align:center;color:var(--white)}
.hex-body h3{font-size:14px;font-weight:700;margin:36px 0 10px;white-space:nowrap}
.hex-body p{font-size:11px;line-height:16px;padding:0 10px}

/* Contact */
.contact{position:absolute;top:1860px;left:0;width:1200px;height:400px;overflow:hidden}
.contact-photo{position:absolute;inset:0;background:linear-gradient(100deg,#e9e9e7 0%,#f7f7f5 30%,#f7f7f5 65%,#d9dad8 100%)}
.contact-title{position:absolute;top:34px;left:0;width:1200px;text-align:center;font-size:32px;font-weight:600;color:var(--ink)}
.contact-sub{position:absolute;top:92px;left:310px;width:580px;text-align:center;font-size:14px;line-height:22px;color:var(--text)}
.field{position:absolute;background:var(--white);border:1px solid var(--line);font-size:12px;color:var(--muted);padding:8px 12px}
.submit{position:absolute;top:322px;left:536px;width:128px;height:34px;line-height:34px;font-size:12px}

/* Footer */
.footer{position:absolute;top:2260px;left:0;width:1200px;height:320px;background:var(--white)}
.col{position:absolute;top:30px}
.col h4{font-size:20px;font-weight:400;color:var(--orange);margin-bottom:10px}
.col li{list-style:none;font-size:14px;line-height:22px;color:var(--text)}
.social{display:flex;gap:8px}
.social span{width:28px;height:28px;border-radius:50%;background:var(--orange)}
.foot-brand{position:absolute;top:50px;left:880px;display:flex;align-items:center;gap:10px;font-size:32px;font-weight:600;color:var(--ink)}
.foot-brand .brand-mark{background:var(--ink)}
.foot-rule{position:absolute;top:222px;left:160px;width:880px;height:1px;background:var(--line)}
.copyright{position:absolute;top:258px;left:0;width:1200px;text-align:center;font-size:11px;color:var(--muted)}
</style>
</head>
<body>

<header class="hero">
  <div class="hero-photo" role="img" aria-label="Photo of a laptop on a bright desk beside a potted plant"></div>
  <div class="hero-shade"></div>
  <nav class="nav">
    <div class="brand"><span class="brand-mark"></span>quorvix</div>
    <div class="nav-links">
      <span>Solutions</span><span>Pricing</span><span>Company</span><span class="nav-cta">Get free Quote</span>
    </div>
  </nav>
  <h1 class="hero-title">Turn Websites Into Structured Data feeds</h1>
  <p class="hero-sub">Easily get structured data feeds from any website through our cloud based data as a service platform. No programming, Servers or Expensive Software required</p>
  <span class="btn hero-btn">Get Free Quote</span>
</header>
<div class="dots"><span class="dot"></span><span class="dot active"></span><span class="dot"></span><span class="dot"></span></div>

<h2 class="clients-title">Clients we work</h2>
<div class="container clients">
  <div class="client">Halvern</div>
  <div class="client">Launchwell</div>
  <div class="client">Tasklane</div>
  <div class="client">Meridane</div>
  <div class="client">Corbelt</div>
  <div class="client">Zentrik</div>
</div>

<section class="uses">
  <h2 class="uses-title">Businesses of all sizes use our clean data feeds to Quickly build apps,<br>Experiment with fresh ideas and Solve business problems</h2>

  <div class="use left" style="top:196px"><h3>ECommerce</h3><p>Our ecommerce product data feeds give you pricing and catalog insight across every store.</p></div>
  <div class="use-icon left" style="top:200px"></div>
  <div class="use-icon right" style="top:200px"></div>
  <div class="use right" style="top:196px"><h3>News Aggregation</h3><p>We help businesses build their own unique news feed by aggregating articles from many sites.</p></div>

  <div class="use left" style="top:310px"><h3>Lead Generation</h3><p>We help firms build their own list of qualified prospects from the public web.</p></div>
  <div class="use-icon left" style="top:314px"></div>
  <div class="use-icon right" style="top:314px"></div>
  <div class="use right" style="top:310px"><h3>Recruiting</h3><p>We help recruiters automate ongoing candidate profile and job collection from online sources.</p></div>

  <div class="use left" style="top:424px"><h3>SERP Tracking</h3><p>Our search result data feeds help marketers track ranking changes for every keyword they need.</p></div>
  <div class="use-icon left" style="top:428px"></div>
  <div class="use-icon right" style="top:428px"></div>
  <div class="use right" style="top:424px"><h3>Build your App</h3><p>We help startups quickly build their apps on top of our reliable clean data.</p></div>
</section>

<h2 class="why-title">Why Us</h2>

<div class="hex" style="left:192px">
  <svg viewBox="0 0 216 280" width="216" height="280"><polygon points="108,0 216,62 216,218 108,280 0,218 0,62" fill="var(--orange)"/><rect x="90" y="60" width="36" height="30" fill="none" stroke="#fff" stroke-width="3"/></svg>
  <div class="hex-body"><h3>Solve Real Problems</h3><p>Custom data solutions that address the real business questions your team faces.</p></div>
</div>
<div class="hex" style="left:412px">
  <svg viewBox="0 0 216 280" width="216" height="280"><polygon points="108,0 216,62 216,218 108,280 0,218 0,62" fill="var(--grey-hex)"/><ellipse cx="108" cy="64" rx="18" ry="6" fill="none" stroke="#fff" stroke-width="3"/><path d="M90 64v24c0 8 36 8 36 0V64" fill="none" stroke="#fff" stroke-width="3"/></svg>
  <div class="hex-body"><h3>Clean Data</h3><p>Validated, deduplicated and structured data delivered ready to use.</p></div>
</div>
<div class="hex" style="left:632px">
  <svg viewBox="0 0 216 280" width="216" height="280"><polygon points="108,0 216,62 216,218 108,280 0,218 0,62" fill="var(--orange)"/><polyline points="88,92 102,76 112,84 128,62" fill="none" stroke="#fff" stroke-width="3"/></svg>
  <div class="hex-body"><h3>Customer Success</h3><p>Dedicated support staff who make sure every feed meets your needs.</p></div>
</div>
<div class="hex" style="left:852px">
  <svg viewBox="0 0 216 280" width="216" height="280"><polygon points="108,0 216,62 216,218 108,280 0,218 0,62" fill="var(--grey-hex)"/><circle cx="108" cy="74" r="16" fill="none" stroke="#fff" stroke-width="3"/><circle cx="108" cy="74" r="5" fill="#fff"/></svg>
  <div class="hex-body"><h3>Data Wrangling Support</h3><p>Our team handles cleaning, mapping and formatting of complex data.</p></div>
</div>

<section class="contact">
  <div class="contact-photo" role="img" aria-label="Photo of a white desk with a keyboard, notebook and pen"></div>
  <h2 class="contact-title">We're here to help!</h2>
  <p class="contact-sub">We're friendly and available to help solve your data extraction problems. Fill the form below to contact us. Let us do the heavy lifting for you.</p>
  <div class="field" style="top:176px;left:300px;width:292px;height:32px">Email address</div>
  <div class="field" style="top:176px;left:608px;width:292px;height:32px">Your Monthly Budget</div>
  <div class="field" style="top:220px;left:300px;width:600px;height:90px">Your Message</div>
  <span class="btn submit">SUBMIT</span>
</section>

<footer class="footer">
  <div class="col" style="left:160px"><h4>Quick Links</h4><ul><li>Blog</li><li>Answers</li><li>Case Studies</li><li>Data</li></ul></div>
  <div class="col" style="left:380px"><h4>Resources</h4><ul><li>Startup Partner program</li><li>FAQ</li><li>Careers</li></ul></div>
  <div class="col" style="left:610px"><h4>Follow Us</h4><div class="social"><span></span><span></span><span></span><span></span></div></div>
  <div class="foot-brand"><span class="brand-mark"></span>quorvix</div>
  <div class="foot-rule"></div>
  <p class="copyright">© 2016 Quorvix. All rights reserved. Terms of Use</p>
</footer>

</body>
</html>
```